New web design for a service provider in the medical field

We are looking for a new design for our website. We are a company that repairs and sells medical endoscopes. Our customers include doctors and hospitals. Our current website can be found at https://lumavex.de/en/lumavex-english.
We need a new web design (without programming) for the following 3 pages:
-Startpage https://lumavex.de/en/lumavex-english/
-Used endoscopes https://lumavex.de/en/used-endoscopes/
-Purchase https://lumavex.de/en/purchase/
The design should be modern and stylish.
The blue color of the logo should be reflected on the page, but not too intrusive.
I have uploaded the images from the header. If more images are needed, let me know and I will upload them.

Target Market(s)
Doctors and hospitals

```html
<!DOCTYPE html>
<html lang="en">
<head>
<meta charset="utf-8">
<title>Lumavex – Used Endoscopes</title>
<link href="https://fonts.googleapis.com/css2?family=Rubik:wght@400;500;600&family=Roboto:wght@400;500&display=swap" rel="stylesheet">
<style>
:root{
  --blue:#2aa3dc;
  --blue-strong:#0a6fb8;
  --navy:#0b4a79;
  --navy-deep:#073a61;
  --ink:#333840;
  --text:#6b7079;
  --soft:#eaf3f8;
  --card:#f6f7f9;
  --line:#e8ebef;
}
*{box-sizing:border-box;margin:0;padding:0}
html,body{width:1200px;height:3651px;overflow:hidden;background:#fff}
body{font-family:'Roboto',sans-serif;color:var(--text);position:relative}
.abs{position:absolute}
h1,h2,h3,h4{font-family:'Rubik',sans-serif;color:var(--ink);font-weight:500}
.accent{color:var(--blue)}
.eyebrow{font-family:'Roboto',sans-serif;font-size:14px;color:var(--ink)}
.center{text-align:center;left:0;width:1200px}

/* top bar */
.topbar{top:0;left:0;width:1200px;height:39px;border-bottom:1px solid var(--line);font-size:11px;color:var(--ink)}
.topbar .item{top:13px;display:flex;align-items:center;gap:8px}
.topbar svg{width:11px;height:11px}
.flag{top:14px;left:900px;width:16px;height:11px;background:#3d5fa8;border-radius:2px}
.social{display:flex;gap:15px;top:15px}
.social span{width:8px;height:8px;border-radius:50%;background:var(--ink);display:block}

/* nav */
.nav{top:39px;left:0;width:1200px;height:72px}
.brand{font-family:'Rubik',sans-serif;font-weight:500;font-size:17px;color:var(--navy);display:flex;align-items:center;gap:8px}
.brand i{width:10px;height:10px;border-radius:50%;background:var(--blue);display:block}
.menu{top:28px;left:330px;display:flex;gap:26px;font-size:11.5px;color:var(--ink)}
.menu .active{color:var(--blue-strong)}
.btn{background:var(--blue-strong);color:#fff;font-size:11.5px;font-weight:500;border-radius:18px;display:flex;align-items:center;justify-content:center}

/* hero */
.hero{top:111px;left:0;width:1200px;height:328px;background:linear-gradient(90deg,#eef0f2 0%,#e4e7ea 45%,#c9ced3 70%,#e9ebed 100%)}
.hero h1{top:110px;left:154px;font-size:37px;font-weight:600}
.hero p{top:168px;left:156px;font-size:11px;line-height:21px;width:360px}

/* intro */
.intro h2{top:572px;left:156px;font-size:34px;line-height:49px;font-weight:600}
.para{font-size:11px;line-height:21.5px}
.intro h4{top:843px;left:156px;font-size:13.5px;font-weight:500}
.perks{top:519px;left:840px;width:204px;height:538px;background:var(--soft);border-radius:10px;text-align:center}
.perk{position:absolute;left:0;width:204px}
.perk svg{width:60px;height:60px;display:block;margin:0 auto 10px}
.perk h3{font-size:13.5px;font-weight:500;margin-bottom:8px}
.perk p{font-size:10.5px}

/* product cards */
.prod{width:402px;background:var(--card);border-radius:8px;overflow:hidden;box-shadow:0 6px 18px rgba(0,0,0,.05)}
.prod .pic{height:270px}
.prod h3{margin:30px 32px 12px;font-size:16px;font-weight:500}
.prod p{margin:0 32px;font-size:10.5px;line-height:20px}
.makers{margin:16px 32px 0;display:flex;gap:32px;font-family:'Rubik',sans-serif;font-size:10px;font-weight:600;color:var(--ink)}
.more{margin:18px 32px 0;font-size:12px;font-weight:500;color:var(--ink);display:flex;align-items:center;gap:14px}
.more svg{width:18px;height:14px}

/* manufacturers */
.maker{top:2546px;width:199px;height:65px;background:#fff;border-radius:6px;box-shadow:0 6px 20px rgba(0,0,0,.07);display:flex;align-items:center;justify-content:center;font-family:'Rubik',sans-serif;font-weight:600;font-size:26px;color:var(--ink)}

/* reasons */
.reason{top:2912px;width:275px;height:201px;background:var(--soft);border-radius:10px;padding:24px 28px}
.reason svg{width:32px;height:32px;margin-bottom:14px}
.reason h3{font-size:13.5px;font-weight:500;margin-bottom:8px}
.reason p{font-size:10.5px;line-height:20px}
.circle-btn{width:32px;height:32px;border:1px solid #9aa1a9;border-radius:50%;display:flex;align-items:center;justify-content:center;background:#fff}
.circle-btn svg{width:14px;height:14px}

/* footer */
.footer{top:3277px;left:0;width:1200px;height:374px;background:var(--navy)}
.cta{top:3215px;left:129px;width:943px;height:132px;background:var(--blue-strong);border-radius:8px}
.cta .eyebrow{position:absolute;top:36px;left:34px;color:#fff;font-size:14px}
.cta h2{position:absolute;top:56px;left:34px;color:#fff;font-size:33px;font-weight:600}
.cta .white{position:absolute;top:59px;left:752px;width:156px;height:35px;background:#fff;color:var(--navy);border-radius:18px;font-size:11px;font-weight:500;display:flex;align-items:center;justify-content:center}
.fcol{top:3408px;color:#fff}
.fcol h4{color:#fff;font-size:13px;font-weight:500;margin-bottom:16px}
.fcol ul{list-style:none;font-size:10px;line-height:24px;color:#dbe6ef}
.fcol p{font-size:10px;line-height:19px;color:#dbe6ef}
.newsletter{margin-top:16px;width:224px;height:32px;background:#fff;border-radius:16px;position:relative;font-size:9px;color:#999;padding:11px 16px}
.newsletter span{position:absolute;right:2px;top:2px;width:28px;height:28px;border-radius:50%;background:var(--blue-strong);display:flex;align-items:center;justify-content:center}
.bottom{top:3602px;left:0;width:1200px;height:49px;background:var(--navy-deep);color:#fff;font-size:10px}
</style>
</head>
<body>

<!-- top bar -->
<div class="abs topbar">
  <div class="abs item" style="left:128px">
    <svg viewBox="0 0 12 12" fill="none" stroke="#7b8a99"><rect x="1" y="2.5" width="10" height="7" rx="1"/><path d="M1 3l5 4 5-4"/></svg>info@lumavex.de
  </div>
  <div class="abs item" style="left:273px">
    <svg viewBox="0 0 12 12" fill="none" stroke="#7b8a99"><path d="M3 1.5l2 2.5-1 1.2a7 7 0 003 3L8.2 7l2.3 2-1 1.5C5 10 2 7 1.5 2.5z"/></svg>+49 4100 555 210-0
  </div>
  <div class="abs" style="top:14px;left:635px">Pick Up Order</div>
  <div class="abs" style="top:14px;left:729px">About US</div>
  <div class="abs" style="top:14px;left:802px">Contact Us</div>
  <div class="abs flag" aria-label="English"></div>
  <div class="abs" style="top:11px;left:924px;font-size:9px;color:#999">⌄</div>
  <div class="abs social" style="left:979px"><span></span><span></span><span></span><span></span></div>
</div>

<!-- nav -->
<div class="abs nav">
  <div class="abs brand" style="left:128px;top:24px"><i></i>Lumavex</div>
  <div class="abs menu">
    <span>Home</span><span>Endoscope Repair</span><span class="active">Used Endoscopes</span><span>Endoscopy Systems</span><span>Endoscopy Accessories</span>
  </div>
  <div class="abs btn" style="left:941px;top:19px;width:131px;height:33px">Purchase Now!</div>
</div>

<!-- hero -->
<section class="abs hero" role="img" aria-label="Close-up of an endoscope control handle in a bright clinic">
  <h1 class="abs">Quality Without <span class="accent">Compromise</span></h1>
  <p class="abs">Lorem ipsum dolor sit amet, consectetur adipiscing sed do eiusmod tempor incididunt ut labore et dolore amet magna aliqua.</p>
</section>

<!-- intro -->
<section class="intro">
  <div class="abs eyebrow" style="top:544px;left:157px">Lorem Ipsum</div>
  <h2 class="abs">Purchase of <span class="accent">Used Endoscopes</span><br>– The Inexpensive Alternative</h2>
  <p class="abs para" style="top:680px;left:157px;width:615px">Used endoscopes are an excellent, high-quality alternative to new equipment for all doctors and hospitals who want to add to their equipment pool cost-effectively. On our website you will find all types of equipment - gastroscopes, coloscopes, bronchoscopes, cystoscopes and duodenoscopes.</p>
  <p class="abs para" style="top:753px;left:157px;width:615px">All used endoscopes that we offer for sale were already in medical use and have been professionally looked after and serviced during this time. In addition, we can offer you endoscopy accessories both for medical examinations and for cleaning and maintaining your endoscopes.</p>
  <h4 class="abs">Quality with warranty for more safety</h4>
  <p class="abs para" style="top:877px;left:157px;width:615px">After the purchase, our technicians subjected the devices to extensive technical tests and overhauled them. Last but not least, we rely on well-known brands that themselves stand for a high quality standard – Kestral, Meridan and Halvor. For these reasons we can offer a twelve month warranty on our used equipment!</p>
  <p class="abs para" style="top:951px;left:157px;width:615px">Only tested quality leaves our company: To ensure the highest quality standards, we carry out an intensive outgoing inspection on every device before dispatch. We enclose documentation of the test result with your endoscope and archive it for future reference.</p>

  <aside class="abs perks">
    <div class="perk" style="top:45px">
      <svg viewBox="0 0 60 60" fill="none" stroke="#2aa3dc" stroke-width="2"><circle cx="30" cy="28" r="22"/><circle cx="30" cy="28" r="16"/><path d="M14 44l-4 10 8-3 4 6 4-10M46 44l4 10-8-3-4 6-4-10"/><text x="30" y="31" text-anchor="middle" font-family="Rubik" font-size="13" fill="#2aa3dc" stroke="none">12</text><text x="30" y="38" text-anchor="middle" font-family="Roboto" font-size="5" fill="#2aa3dc" stroke="none">MONTHS</text></svg>
      <h3>12 months warranty</h3><p>Highest quality standards</p>
    </div>
    <div class="perk" style="top:210px">
      <svg viewBox="0 0 60 60" fill="none" stroke="#2aa3dc" stroke-width="2"><circle cx="30" cy="22" r="10"/><path d="M16 22a14 14 0 0128 0v4M16 22v5h4v-5M44 22v5h-4v-5M12 56c0-10 8-16 18-16s18 6 18 16z"/></svg>
      <h3>Best customer service</h3><p>We are there for you</p>
    </div>
    <div class="perk" style="top:373px">
      <svg viewBox="0 0 60 60" fill="none" stroke="#2aa3dc" stroke-width="2"><circle cx="30" cy="30" r="24"/><ellipse cx="30" cy="30" rx="10" ry="24"/><path d="M6 30h48M10 18h40M10 42h40"/></svg>
      <h3>Worldwide shipping</h3><p>Our service knows no borders!</p>
    </div>
  </aside>
</section>

<!-- products -->
<section>
  <div class="abs eyebrow center" style="top:1125px">Lorum Ipsum Dolor</div>
  <h2 class="abs center" style="top:1155px;font-size:34px;font-weight:600"><span class="accent">Used</span> Device - <span class="accent">Fair</span> Price - <span class="accent">Full</span> Performance</h2>
  <p class="abs para center" style="top:1218px;padding:0 260px">Lorem ipsum dolor sit amet, consectetur adipiscing elit, sed do eiusmod tempor incididunt ut labore et dolore magna aliqua. Ut enim ad minim veniam, quis nostrud exercitation ullamco laboris nisi ut aliquip ex ea commodo consequat. Duis aute irure</p>

  <article class="abs prod" style="top:1299px;left:176px;height:447px">
    <div class="pic" role="img" aria-label="Flexible video endoscopes hanging on a wall rack" style="background:linear-gradient(180deg,#eceef0,#c9cdd1)"></div>
    <h3>Flexible Video Endoscopes</h3>
    <p>Discover our flexible endoscopes from the best brands such as Kestral, Meridan and Halvor: gastroscopes, coloscopes, bronchoscopes, duodenoscopes, cystoscopes and more.</p>
    <div class="makers"><span>KESTRAL</span><span>MERIDAN</span><span>HALVOR</span></div>
  </article>
  <article class="abs prod" style="top:1299px;left:622px;height:447px">
    <div class="pic" role="img" aria-label="Video processor and light source units with warm light flare" style="background:linear-gradient(135deg,#f0a070,#e8e6e4 45%,#b8bec6)"></div>
    <h3>Processors &amp; Light-Sources</h3>
    <p>Provide better diagnosis to your patients by means of high-resolution imaging, implemented by the best video processors of the latest generation.</p>
    <div class="makers"><span>KESTRAL</span><span>MERIDAN</span><span>HALVOR</span></div>
  </article>
  <article class="abs prod" style="top:1792px;left:176px;height:454px">
    <div class="pic" role="img" aria-label="Technician working at an endoscopy tower with monitor" style="background:linear-gradient(135deg,#dfe2e5,#f4f5f6 50%,#c5cbd1)"></div>
    <h3>Endoscopy Systems</h3>
    <p>We help you with configuring a complete endoscopy system for your needs and requirements - from the endoscope to the peripheral devices (processor, light source, screen, suction pump, etc.).</p>
    <div class="more">Learn all about Endoscopy Systems <svg viewBox="0 0 18 14" fill="none" stroke="#0a6fb8" stroke-width="2"><path d="M1 7h15M10 1l6 6-6 6"/></svg></div>
  </article>
  <article class="abs prod" style="top:1792px;left:622px;height:454px">
    <div class="pic" role="img" aria-label="Endoscopy accessories and scope on a turquoise drape" style="background:linear-gradient(160deg,#e3a860,#5fb3bf 40%,#3a98a6)"></div>
    <h3>Accesories</h3>
    <p>Cover your needs for consumables for single or multiple specific use - from biopsy forceps to cleaning brushes and much more.</p>
    <div class="more">Find your accessories here! <svg viewBox="0 0 18 14" fill="none" stroke="#0a6fb8" stroke-width="2"><path d="M1 7h15M10 1l6 6-6 6"/></svg></div>
  </article>
</section>

<!-- manufacturers -->
<section>
  <div class="abs eyebrow center" style="top:2326px">Lorem Ipsum Dolor</div>
  <h2 class="abs center" style="top:2355px;font-size:34px;line-height:49px;font-weight:600">Second Hand Endoscopes From<br><span class="accent">Leading Manufacturers</span></h2>
  <p class="abs para center" style="top:2472px">Discover our range of second hand and refurbished endoscopes from leading manufacturers.<br>We give a twelve month warranty for this.</p>
  <div class="abs maker" style="left:259px">KESTRAL</div>
  <div class="abs maker" style="left:500px">MERIDAN</div>
  <div class="abs maker" style="left:740px">HALVOR</div>
</section>

<!-- reasons -->
<section>
  <div class="abs eyebrow center" style="top:2690px">Lorem Ipsum Dolor</div>
  <h2 class="abs center" style="top:2719px;font-size:34px;line-height:49px;font-weight:600">We are Your First Choice When Buying<br><span class="accent">Used Endoscopy Equipment</span></h2>
  <p class="abs para center" style="top:2830px;padding:0 260px">Lorem ipsum dolor sit amet, consectetur adipiscing elit, sed do eiusmod tempor incididunt ut labore et dolore magna aliqua. Ut enim ad minim veniam, quis nostrud exercitation ullamco laboris nisi ut aliquip ex ea commodo consequat. Duis aute irure</p>

  <div class="abs circle-btn" style="top:2995px;left:112px"><svg viewBox="0 0 14 14" fill="none" stroke="#555" stroke-width="1.5"><path d="M13 7H1M6 2L1 7l5 5"/></svg></div>
  <div class="abs circle-btn" style="top:2995px;left:1056px"><svg viewBox="0 0 14 14" fill="none" stroke="#555" stroke-width="1.5"><path d="M1 7h12M8 2l5 5-5 5"/></svg></div>

  <div class="abs reason" style="left:156px">
    <svg viewBox="0 0 32 32" fill="none" stroke="#2aa3dc" stroke-width="2"><circle cx="16" cy="16" r="5"/><path d="M16 2v5M16 25v5M2 16h5M25 16h5M6 6l3.5 3.5M22.5 22.5L26 26M6 26l3.5-3.5M22.5 9.5L26 6"/></svg>
    <h3>As New Equipment</h3>
    <p>The devices have already been in medical use before but were professionally maintained and serviced. Consumable parts were completely renewed after purchase by ...</p>
  </div>
  <div class="abs reason" style="left:463px">
    <svg viewBox="0 0 32 32" fill="none" stroke="#2aa3dc" stroke-width="2"><circle cx="16" cy="16" r="14"/><path d="M12 23V9h6a4 4 0 010 8h-6M17 17l5 6"/></svg>
    <h3>Brand Manufacturers</h3>
    <p>We primarily offer the brands Kestral, Meridan and Halvor, which are characterized by long-lasting quality and whose manufacturers have already earned ...</p>
  </div>
  <div class="abs reason" style="left:769px">
    <svg viewBox="0 0 32 32" fill="none" stroke="#2aa3dc" stroke-width="3"><circle cx="13" cy="13" r="9"/><path d="M20 20l9 9"/></svg>
    <h3>Tested &amp; Overhauled</h3>
    <p>Our trained technicians have checked and overhauled every device in a variety of ways before it is offered for resale.</p>
  </div>
</section>

<!-- footer -->
<footer>
  <div class="abs footer"></div>
  <div class="abs cta">
    <div class="eyebrow">Get In Touch</div>
    <h2>How Can We Help You?</h2>
    <div class="white">Contact Us Now</div>
  </div>

  <div class="abs fcol" style="left:156px;top:3412px">
    <div class="brand" style="color:#fff"><i style="background:#fff"></i>Lumavex</div>
    <ul style="margin-top:34px">
      <li>☏ &nbsp;+49 4100 555 210-0</li>
      <li>✉ &nbsp;info@lumavex.de</li>
    </ul>
    <div class="social" style="display:flex;gap:28px;margin-top:10px"><span style="background:#fff;width:7px;height:7px;border-radius:50%"></span><span style="background:#fff;width:7px;height:7px;border-radius:50%"></span><span style="background:#fff;width:7px;height:7px;border-radius:50%"></span><span style="background:#fff;width:7px;height:7px;border-radius:50%"></span></div>
  </div>
  <div class="abs fcol" style="left:430px">
    <h4>Quick Links</h4>
    <ul><li>Home</li><li>Endoscope Repair</li><li>Used Endoscopes</li><li>Endoscopy Systems</li><li>Endoscopy Accessories</li></ul>
  </div>
  <div class="abs fcol" style="left:661px">
    <h4>Usefull Links</h4>
    <ul><li>Information</li><li>About Us</li><li>Contact Us</li><li>TOS</li><li>FAQ</li></ul>
  </div>
  <div class="abs fcol" style="left:820px;width:224px">
    <h4>Newsletter</h4>
    <p>Lorem ipsum dolor sit consectetur adipiscing elit sed do eiusmod tempor incididunt ut labore et dolore magna aliqua.</p>
    <div class="newsletter">Your Email<span><svg width="12" height="12" viewBox="0 0 12 12" fill="none" stroke="#fff" stroke-width="1.2"><path d="M1 6l10-5-4 10-1.5-4z"/></svg></span></div>
  </div>

  <div class="abs bottom">
    <span class="abs" style="left:156px;top:20px">2022 All rights reserved</span>
    <span class="abs" style="left:856px;top:20px">Privacy Policy</span>
    <span class="abs" style="left:955px;top:20px">Terms &amp; Conditions</span>
  </div>
</footer>

</body>
</html>
```